RW Framewell Inc Business cards

We need business cards using our existing logo but slightly modified. Right now the logo says RW Loadbearing Masonry. We want to keep the RW part of the design, but replace the Structural Concrete portion with "FRAMEWELL". Please see the attached file.
Ideally this would be a blank template so we can add Different Names, titles, and phone numbers later.
On the one side we want only the logo and on the other side the detail. I'm attaching an example for you to see.
Please reach out with any other questions. Our address and other details will be given out once we find a design we like.

Target Market(s)

Construction Industry

```html
<!DOCTYPE html>
<html lang="en">
<head>
<meta charset="utf-8">
<title>RW Framewell Inc – Business Cards</title>
<link rel="stylesheet" href="https://fonts.googleapis.com/css2?family=Montserrat:wght@600&family=Roboto:wght@400;700&display=swap">
<style>
  :root {
    --backdrop: #c9c9c9;
    --card: #f7f7f6;
    --brand-blue: #2f62ad;
    --brand-grey: #6f6f6f;
    --text-grey: #5c5c5c;
    --white: #ffffff;
  }
  * { box-sizing: border-box; margin: 0; padding: 0; }
  html, body { width: 1200px; height: 852px; overflow: hidden; }
  body {
    background: var(--backdrop);
    font-family: "Roboto", Arial, sans-serif;
    display: flex;
    align-items: center;
    justify-content: center;
    gap: 40px;
  }
  .card {
    position: relative;
    width: 540px;
    height: 310px;
    background: var(--card);
    border-radius: 22px;
    overflow: hidden;
    box-shadow: 0 6px 14px rgba(0,0,0,0.18);
  }
  /* Logo lockup: plain wordmark with square */
  .wordmark {
    display: flex;
    align-items: center;
    gap: 12px;
    font-family: "Montserrat", Arial, sans-serif;
    font-weight: 600;
    color: var(--brand-blue);
    letter-spacing: 0.08em;
    white-space: nowrap;
  }
  .wordmark__square {
    width: 26px; height: 26px;
    background: var(--brand-grey);
    flex: none;
  }
  /* Front */
  .card--front .wordmark {
    position: absolute;
    left: 50%; top: 44%;
    transform: translate(-50%, -50%);
    font-size: 34px;
  }
  .edge-band {
    position: absolute;
    left: 0; right: 0; bottom: 0;
    height: 14px;
    display: flex;
  }
  .edge-band__grey { flex: 0 0 45%; background: var(--brand-grey); }
  .edge-band__blue { flex: 1; background: var(--brand-blue); }
  /* Back */
  .card--back .wordmark {
    position: absolute;
    left: 30px; top: 50%;
    transform: translateY(-50%);
    font-size: 21px;
    gap: 9px;
  }
  .card--back .wordmark__square { width: 18px; height: 18px; }
  .details {
    position: absolute;
    left: 300px; top: 52px;
    color: var(--text-grey);
  }
  .details__name {
    font-size: 22px;
    font-weight: 700;
    color: var(--brand-blue);
    line-height: 1.1;
  }
  .details__title { font-size: 13px; margin-bottom: 16px; }
  .contact { list-style: none; font-size: 13px; line-height: 1.55; }
  .contact__row { display: flex; align-items: flex-start; gap: 10px; }
  .contact__icon { width: 13px; height: 13px; margin-top: 3px; flex: none; fill: var(--text-grey); }
  .division-tab {
    position: absolute;
    right: 0; bottom: 0;
    width: 232px; height: 40px;
    background: var(--brand-blue);
    border-top-left-radius: 18px;
    color: var(--white);
    font-weight: 700;
    font-size: 14px;
    display: flex; align-items: center; justify-content: center;
  }
  .edge-band--back .edge-band__grey { flex: 0 0 100%; }
  .edge-band--back { height: 6px; }
</style>
</head>
<body>

  <section class="card card--front" aria-label="Card front">
    <div class="wordmark"><span class="wordmark__square"></span>RW FRAMEWELL</div>
    <div class="edge-band"><span class="edge-band__grey"></span><span class="edge-band__blue"></span></div>
  </section>

  <section class="card card--back" aria-label="Card back">
    <div class="wordmark"><span class="wordmark__square"></span>RW FRAMEWELL</div>

    <div class="details">
      <p class="details__name">Dana Whitlock</p>
      <p class="details__title">Managing Director</p>
      <ul class="contact">
        <li class="contact__row">
          <svg class="contact__icon" viewBox="0 0 16 16" aria-hidden="true"><path d="M3.5 1l2.5 3-1.5 1.8c.9 2 2.7 3.8 4.7 4.7L11 9l3 2.5-1.5 2.8C7 14 2 9 1.7 3.3z"/></svg>
          <span>555-010-2478</span>
        </li>
        <li class="contact__row">
          <svg class="contact__icon" viewBox="0 0 16 16" aria-hidden="true"><path d="M1 3h14v10H1z M2 4l6 5 6-5" fill="none" stroke="#5c5c5c" stroke-width="1.6"/></svg>
          <span>dana@framewell-example.com</span>
        </li>
        <li class="contact__row">
          <svg class="contact__icon" viewBox="0 0 16 16" aria-hidden="true"><circle cx="8" cy="8" r="6.5" fill="none" stroke="#5c5c5c" stroke-width="1.4"/><path d="M1.5 8h13M8 1.5c-3 3.5-3 9.5 0 13M8 1.5c3 3.5 3 9.5 0 13" fill="none" stroke="#5c5c5c" stroke-width="1.2"/></svg>
          <span>www.framewell-example.com</span>
        </li>
        <li class="contact__row">
          <svg class="contact__icon" viewBox="0 0 16 16" aria-hidden="true"><path d="M8 1a5 5 0 0 1 5 5c0 4-5 9-5 9S3 10 3 6a5 5 0 0 1 5-5zm0 3a2 2 0 1 0 0 4 2 2 0 0 0 0-4z"/></svg>
          <span>48 Girder Lane, Millbrook,<br>Oregon, US 97000</span>
        </li>
      </ul>
    </div>

    <div class="division-tab">RW Loadbearing Masonry</div>
  </section>

</body>
</html>
```